Water ATM Card

Need a design for water ATM cards. Size of card is 3.375 x 2.125 inch
On the Front include the Cedar hollow Logo.
Bottom right corner should have Price $100
On the Back
This card is to be used to access water refills at any Cedar Hollow Water Vending Machines.
Please contact (869) 418 2930 or (869) 534 1276 or email clearflowbox@mailvista.example for any assistance or recharging of card.

```html
<!DOCTYPE html>
<html lang="en">
<head>
<meta charset="utf-8">
<title>Cedar Hollow Water ATM Card</title>
<link href="https://fonts.googleapis.com/css2?family=Montserrat:wght@400;500;700&display=swap" rel="stylesheet">
<style>
  :root {
    --stage: #1f1f1f;
    --card-white: #ffffff;
    --brand-blue: #2b5ca8;
    --brand-green: #34a047;
    --ink: #1c1c1c;
    --back-top: #2f7fbf;
    --back-mid: #3a58a0;
    --back-bottom: #2e3a88;
    --on-dark: #ffffff;
  }
  * { margin: 0; padding: 0; box-sizing: border-box; }
  html, body {
    width: 1200px; height: 1059px; overflow: hidden;
    background: var(--stage);
    font-family: "Montserrat", sans-serif;
  }
  .card {
    position: absolute;
    border-radius: 20px;
    overflow: hidden;
  }
  .card-front {
    left: 256px; top: 89px; width: 688px; height: 391px;
    background: var(--card-white);
  }
  .card-back {
    left: 253px; top: 546px; width: 695px; height: 395px;
    background: linear-gradient(170deg, var(--back-top) 0%, var(--back-mid) 45%, var(--back-bottom) 100%);
  }
  .brand-name {
    position: absolute;
    font-weight: 700;
    white-space: nowrap;
    text-transform: uppercase;
    transform: translateX(-50%);
  }
  .card-front .brand-name {
    left: 184px; top: 198px;
    font-size: 21px;
    color: var(--brand-blue);
  }
  .divider {
    position: absolute; left: 332px; top: 118px;
    width: 1.5px; height: 156px;
    background: var(--brand-blue);
  }
  .contact-block {
    position: absolute; left: 345px; top: 116px;
    color: var(--ink);
  }
  .person-name {
    font-size: 22px; font-weight: 700;
    color: var(--brand-blue);
    letter-spacing: 0.3px;
    line-height: 1.1;
  }
  .person-role {
    font-size: 13px; font-weight: 500;
    letter-spacing: 0.6px;
    margin-top: 4px;
  }
  .contact-list { list-style: none; margin-top: 22px; }
  .contact-list li {
    display: flex; align-items: center;
    font-size: 14px; font-weight: 500;
    height: 24px;
  }
  .contact-list li svg { width: 14px; height: 14px; margin-right: 7px; flex: none; fill: var(--brand-blue); }
  .price {
    position: absolute; right: 47px; top: 320px;
    font-size: 19px; font-weight: 700;
    color: var(--brand-green);
  }
  .card-band {
    position: absolute; left: 0; bottom: 0;
    width: 688px; height: 15px;
  }
  .card-back .brand-name {
    left: 50%; top: 205px;
    font-size: 44px;
    color: var(--on-dark);
    letter-spacing: 1px;
  }
  .back-note {
    position: absolute; left: 0; right: 0; top: 334px;
    text-align: center;
    font-size: 14px; font-weight: 400;
    color: var(--on-dark);
  }
</style>
</head>
<body>

<section class="card card-front" aria-label="Card front">
  <div class="brand-name">Cedar Hollow</div>
  <div class="divider"></div>
  <div class="contact-block">
    <div class="person-name">DANIEL REYES</div>
    <div class="person-role">OWER</div>
    <ul class="contact-list">
      <li>
        <svg viewBox="0 0 24 24" aria-hidden="true"><path d="M6.6 10.8a15.1 15.1 0 0 0 6.6 6.6l2.2-2.2a1 1 0 0 1 1-.25 11.4 11.4 0 0 0 3.6.57 1 1 0 0 1 1 1V20a1 1 0 0 1-1 1A17 17 0 0 1 3 4a1 1 0 0 1 1-1h3.5a1 1 0 0 1 1 1c0 1.25.2 2.45.57 3.57a1 1 0 0 1-.25 1z"/></svg>
        (869) 418 2930
      </li>
      <li>
        <svg viewBox="0 0 24 24" aria-hidden="true"><path d="M7 1h10a2 2 0 0 1 2 2v18a2 2 0 0 1-2 2H7a2 2 0 0 1-2-2V3a2 2 0 0 1 2-2zm0 3v14h10V4zm5 15.5a1 1 0 1 0 0 2 1 1 0 0 0 0-2z"/></svg>
        (869) 534 1276
      </li>
      <li>
        <svg viewBox="0 0 24 24" aria-hidden="true"><path d="M2 5h20v2l-10 6L2 7zm0 4.3 10 6 10-6V19H2z"/></svg>
        clearflowbox@mailvista.example
      </li>
      <li>
        <svg viewBox="0 0 24 24" aria-hidden="true"><path d="M12 2a10 10 0 1 0 0 20 10 10 0 0 0 0-20zm0 2c.9 1.2 1.6 2.9 1.9 5h-3.8c.3-2.1 1-3.8 1.9-5zM4.3 13h3.8c.1 1.1.2 2.1.5 3H5.5a8 8 0 0 1-1.2-3zm0-2a8 8 0 0 1 1.2-3h3.1c-.3.9-.4 1.9-.5 3zm7.7 9c-.9-1.2-1.6-2.9-1.9-5h3.8c-.3 2.1-1 3.8-1.9 5zm3.9-7h3.8a8 8 0 0 1-1.2 3h-3.1c.3-.9.4-1.9.5-3zm0-2c-.1-1.1-.2-2.1-.5-3h3.1a8 8 0 0 1 1.2 3z"/></svg>
        www.cedarhollow.example
      </li>
    </ul>
  </div>
  <div class="price">Price $100</div>
  <svg class="card-band" viewBox="0 0 688 15" preserveAspectRatio="none" aria-hidden="true">
    <polygon points="0,0 331,0 345,15 0,15" fill="var(--brand-blue)"/>
    <polygon points="341,0 688,0 688,15 355,15" fill="var(--brand-green)"/>
  </svg>
</section>

<section class="card card-back" aria-label="Card back">
  <div class="brand-name">Cedar Hollow</div>
  <p class="back-note">for any assistance or recharging of card.</p>
</section>

</body>
</html>
```